Business Card - connecting 2 souls and beggining the journey of self discovery

Logo on the front
with tag line

On the back list of services and contact details

Seminars
workshops
Coaching
podcasts

Darren Whitlow
Health & Wellbeing Life Coach
0491 372 615
darren@brightcoreliving.example
brightcoreliving.example

Industry/Entity Type

Life Coaching

Contact Information for Business Card

I like the use of colour from the logo to be used. I'm not a fan of white.

Requirements
Must have
• My tagline: every path begins within
Nice to have
• Use of colour that is in the mind body soul logo

```html
<!DOCTYPE html>
<html lang="en">
<head>
<meta charset="utf-8">
<title>Brightcore Living – Business Card</title>
<link href="https://fonts.googleapis.com/css2?family=Open+Sans:ital,wght@0,400;0,600;0,700;1,400&display=swap" rel="stylesheet">
<style>
  :root {
    --purple: #8952a5;
    --grey: #8a8a8a;
    --grey-dark: #7b7b7b;
    --white: #ffffff;
    --backdrop: #ecebe8;
    --band-start: #4fb3a9;
    --band-mid: #8fc9c2;
    --band-end: #c9a6dc;
  }
  * { margin: 0; padding: 0; box-sizing: border-box; }
  html, body { width: 1200px; height: 1000px; overflow: hidden; }
  body {
    background: var(--backdrop);
    font-family: "Open Sans", Arial, sans-serif;
    position: relative;
  }
  .card {
    position: absolute;
    top: 351px;
    width: 520px;
    height: 298px;
    border-radius: 28px;
    overflow: hidden;
    background: var(--white);
    box-shadow: 0 6px 18px rgba(0,0,0,0.18);
  }
  .card--contact { left: 40px; }
  .card--brand { left: 640px; }
  .card__art { position: absolute; inset: 0; width: 100%; height: 100%; }

  .contact { position: absolute; left: 40px; top: 58px; }
  .contact__name { color: var(--purple); font-weight: 700; font-size: 21px; line-height: 1.2; }
  .contact__title { color: var(--grey); font-size: 16px; line-height: 1.3; margin-bottom: 12px; }
  .contact__line { color: var(--grey); font-size: 14px; line-height: 1.35; }
  .contact__line--phone { font-size: 13px; }

  .services {
    position: absolute; left: 36px; right: 36px; bottom: 20px;
    display: flex; justify-content: space-between; list-style: none;
    color: var(--white); font-size: 15px; font-weight: 600;
  }
  .services li::before {
    content: ""; display: inline-block; width: 7px; height: 7px;
    border-radius: 50%; background: var(--white);
    margin-right: 8px; vertical-align: middle;
  }

  .brand { position: absolute; left: 34px; top: 116px; }
  .brand__mark {
    width: 88px; height: 88px; border-radius: 50%;
    background: var(--purple); margin-left: 85px; margin-bottom: 16px;
  }
  .brand__name { color: var(--grey-dark); font-size: 22px; font-weight: 600; letter-spacing: -0.3px; line-height: 1.2; }
  .brand__tagline { color: var(--grey); font-size: 13.5px; font-style: italic; margin-left: 4px; }
</style>
</head>
<body>

  <section class="card card--contact" aria-label="Contact side">
    <svg class="card__art" viewBox="0 0 425 243" preserveAspectRatio="none" aria-hidden="true">
      <defs>
        <linearGradient id="bandContact" x1="0" y1="0" x2="1" y2="0">
          <stop offset="0" stop-color="var(--band-start)"/>
          <stop offset="0.55" stop-color="var(--band-mid)"/>
          <stop offset="1" stop-color="var(--band-end)"/>
        </linearGradient>
      </defs>
      <path d="M0,196 C190,200 335,160 425,52 L425,243 L0,243 Z" fill="var(--purple)"/>
      <path d="M0,190 C190,194 330,150 425,30 L425,48 C332,158 190,197 0,193 Z" fill="url(#bandContact)"/>
    </svg>
    <div class="contact">
      <p class="contact__name">Darren Whitlow</p>
      <p class="contact__title">Life Coach</p>
      <p class="contact__line contact__line--phone">0491 372 615</p>
      <p class="contact__line">www.brightcoreliving.example</p>
      <p class="contact__line">darren@brightcoreliving.example</p>
    </div>
    <ul class="services">
      <li>Seminars</li>
      <li>Workshops</li>
      <li>Coaching</li>
      <li>Podcasts</li>
    </ul>
  </section>

  <section class="card card--brand" aria-label="Brand side">
    <svg class="card__art" viewBox="0 0 425 243" preserveAspectRatio="none" aria-hidden="true">
      <defs>
        <linearGradient id="bandBrand" x1="0" y1="0" x2="1" y2="0">
          <stop offset="0" stop-color="var(--band-start)"/>
          <stop offset="0.55" stop-color="var(--band-mid)"/>
          <stop offset="1" stop-color="var(--band-end)"/>
        </linearGradient>
      </defs>
      <path d="M0,0 H425 V122 C360,70 200,44 0,60 Z" fill="var(--purple)"/>
      <path d="M0,60 C200,40 360,64 425,122 L425,142 C355,78 200,52 0,64 Z" fill="url(#bandBrand)"/>
    </svg>
    <div class="brand">
      <div class="brand__mark"></div>
      <p class="brand__name">Brightcore Living</p>
      <p class="brand__tagline">“ every path begins within ”</p>
    </div>
  </section>

</body>
</html>
```